Velmora Freightway Solutions Business cards

Would like a very unique design catchy but professional for business cards. Please use log provided.Marlon WellsCeo and Founder TransCon Logistix Solutions1-888-913-3225mwells@tlsolutionsus.comwww.tlsolutionsus.com

```html
<!DOCTYPE html>
<html lang="en">
<head>
<meta charset="utf-8">
<title>Velmora Freightway Solutions – Business Card</title>
<link href="https://fonts.googleapis.com/css2?family=Questrial&display=swap" rel="stylesheet">
<style>
  :root {
    --navy: #1f4f8f;
    --blue-deep: #0b3b86;
    --red: #c8202a;
    --card-light: #f4f4f3;
    --card-shade: #e3e2df;
    --page: #d8d3cb;
    --text-blue: #2a5590;
  }
  html, body {
    margin: 0;
    padding: 0;
    width: 1200px;
    height: 970px;
    overflow: hidden;
    background: var(--page);
    font-family: "Questrial", sans-serif;
  }
  .card {
    position: absolute;
    left: 100px;
    top: 200px;
    width: 1000px;
    height: 570px;
    background: linear-gradient(135deg, var(--card-light) 0%, #ecebea 55%, var(--card-shade) 100%);
    box-shadow: 0 10px 30px rgba(0,0,0,0.18);
    overflow: hidden;
  }
  .card-swoosh {
    position: absolute;
    inset: 0;
    width: 100%;
    height: 100%;
  }
  .brand {
    position: absolute;
    left: 68px;
    top: 178px;
    display: flex;
    align-items: center;
    gap: 16px;
  }
  .brand-square {
    width: 36px;
    height: 36px;
    background: var(--red);
  }
  .brand-name {
    font-size: 36px;
    color: var(--navy);
    letter-spacing: 0.5px;
    white-space: nowrap;
  }
  .person {
    position: absolute;
    left: 64px;
    top: 326px;
  }
  .person-name {
    font-size: 34px;
    color: var(--text-blue);
    line-height: 1.05;
  }
  .person-title {
    font-size: 25px;
    color: var(--red);
    line-height: 1.1;
  }
  .contacts {
    position: absolute;
    left: 64px;
    top: 424px;
    margin: 0;
    padding: 0;
    list-style: none;
  }
  .contact {
    display: flex;
    align-items: center;
    gap: 14px;
    height: 35px;
    font-size: 24px;
    color: var(--text-blue);
  }
  .contact-icon {
    width: 30px;
    height: 30px;
    flex: none;
  }
</style>
</head>
<body>
  <main class="card">
    <svg class="card-swoosh" viewBox="0 0 1040 592" preserveAspectRatio="none" aria-hidden="true">
      <path d="M840,0 L1040,0 L1040,592 L835,592 C895,480 932,400 930,300 C926,180 885,80 840,0 Z" fill="var(--blue-deep)"/>
      <path d="M840,0 C885,80 926,180 930,300 C932,400 895,480 835,592" fill="none" stroke="#ffffff" stroke-width="6"/>
      <path d="M665,0 L832,0 C875,80 915,185 922,295 C890,170 800,60 665,0 Z" fill="var(--red)"/>
    </svg>

    <div class="brand">
      <span class="brand-square"></span>
      <span class="brand-name">Velmora Freightway Solutions</span>
    </div>

    <div class="person">
      <div class="person-name">Dorian Pike</div>
      <div class="person-title">Ceo and Founder</div>
    </div>

    <ul class="contacts">
      <li class="contact">
        <svg class="contact-icon" viewBox="0 0 30 30" aria-hidden="true">
          <circle cx="15" cy="15" r="14" fill="var(--red)"/>
          <rect x="10.5" y="7" width="9" height="16" rx="1.5" fill="none" stroke="#fff" stroke-width="1.6"/>
          <circle cx="15" cy="20" r="1" fill="#fff"/>
        </svg>
        <span>1-888-470-6158</span>
      </li>
      <li class="contact">
        <svg class="contact-icon" viewBox="0 0 30 30" aria-hidden="true">
          <circle cx="15" cy="15" r="14" fill="var(--red)"/>
          <rect x="8" y="10" width="14" height="10" fill="none" stroke="#fff" stroke-width="1.6"/>
          <path d="M8,10 L15,16 L22,10" fill="none" stroke="#fff" stroke-width="1.6"/>
        </svg>
        <span>dpike@vfwayroutes.com</span>
      </li>
      <li class="contact">
        <svg class="contact-icon" viewBox="0 0 30 30" aria-hidden="true">
          <circle cx="15" cy="15" r="14" fill="var(--red)"/>
          <circle cx="15" cy="15" r="7.5" fill="none" stroke="#fff" stroke-width="1.5"/>
          <ellipse cx="15" cy="15" rx="3.2" ry="7.5" fill="none" stroke="#fff" stroke-width="1.2"/>
          <path d="M7.5,15 H22.5" stroke="#fff" stroke-width="1.2"/>
        </svg>
        <span>www.vfwayroutes.com</span>
      </li>
    </ul>
  </main>
</body>
</html>
```